Step and Repeat Backdrop for wedding reception photo booth

Would like to have a Step and Repeat Backdrop (8 foot high by 10 foot wide) that incorporates the wedding logo (attached) and the names Helen and Gavin. Background should be white, and wedding colors are burgundy and gold. Show me creativity :-) I have included some random samples.

```html
<!DOCTYPE html>
<html lang="en">
<head>
<meta charset="utf-8">
<title>Helen &amp; Gavin — Step and Repeat Backdrop</title>
<link rel="stylesheet" href="https://fonts.googleapis.com/css2?family=Playfair+Display:wght@500;600;700&display=swap">
<style>
  :root {
    --burgundy: #7d1524;
    --gold: #b38d4c;
    --gold-light: #cfae6e;
    --white: #ffffff;
  }
  html, body {
    margin: 0;
    padding: 0;
    width: 1200px;
    height: 1000px;
    overflow: hidden;
    background: var(--burgundy);
  }
  .backdrop {
    position: relative;
    width: 1200px;
    height: 1000px;
    background: var(--burgundy);
  }
  .backdrop__field {
    position: absolute;
    left: 100px;
    top: 100px;
    width: 1000px;
    height: 798px;
    background: var(--white);
  }
  .repeat-grid {
    position: absolute;
    left: 27px;
    top: 20px;
    display: grid;
    grid-template-columns: repeat(8, 118px);
    grid-template-rows: repeat(12, 63px);
  }
  .tile {
    display: flex;
    align-items: center;
    justify-content: center;
  }
  .monogram {
    font-family: "Playfair Display", serif;
    font-weight: 600;
    font-size: 42px;
    letter-spacing: -1px;
    color: var(--gold);
    line-height: 1;
  }
  .names {
    width: 101px;
    height: 43px;
    background: var(--gold);
    margin: 0 auto;
    display: flex;
    flex-direction: column;
    align-items: center;
    justify-content: center;
    font-family: "Playfair Display", serif;
    font-weight: 600;
    font-size: 19px;
    line-height: 0.95;
    letter-spacing: 0.5px;
    color: var(--white);
    text-transform: uppercase;
  }
  .feature {
    grid-column: 3 / 7;
    grid-row: 4 / 10;
    margin: 2px 8px 8px 8px;
    background: var(--burgundy);
    display: flex;
    flex-direction: column;
    align-items: center;
    justify-content: center;
    gap: 10px;
  }
  .feature__ornament {
    width: 290px;
    height: 74px;
    border-radius: 37px;
    background: radial-gradient(ellipse at center, rgba(207,174,110,0.55), rgba(179,141,76,0.15) 70%, rgba(179,141,76,0) 100%);
  }
  .feature__monogram {
    font-family: "Playfair Display", serif;
    font-weight: 600;
    font-size: 96px;
    letter-spacing: -2px;
    color: var(--gold-light);
    line-height: 1;
  }
</style>
</head>
<body>
<main class="backdrop">
  <section class="backdrop__field">
    <div class="repeat-grid">
      <div class="feature">
        <div class="feature__ornament" role="img" aria-label="Gold flourish ornament above the monogram"></div>
        <div class="feature__monogram">H&amp;G</div>
        <div class="feature__ornament" role="img" aria-label="Gold flourish ornament below the monogram"></div>
      </div>

      <!-- row 1 -->
      <div class="tile"><span class="monogram">H&amp;G</span></div>
      <div class="tile"><div class="names"><span>Helen</span><span>Gavin</span></div></div>
      <div class="tile"><span class="monogram">H&amp;G</span></div>
      <div class="tile"><div class="names"><span>Helen</span><span>Gavin</span></div></div>
      <div class="tile"><span class="monogram">H&amp;G</span></div>
      <div class="tile"><div class="names"><span>Helen</span><span>Gavin</span></div></div>
      <div class="tile"><span class="monogram">H&amp;G</span></div>
      <div class="tile"><div class="names"><span>Helen</span><span>Gavin</span></div></div>
      <!-- row 2 -->
      <div class="tile"><div class="names"><span>Helen</span><span>Gavin</span></div></div>
      <div class="tile"><span class="monogram">H&amp;G</span></div>
      <div class="tile"><div class="names"><span>Helen</span><span>Gavin</span></div></div>
      <div class="tile"><span class="monogram">H&amp;G</span></div>
      <div class="tile"><div class="names"><span>Helen</span><span>Gavin</span></div></div>
      <div class="tile"><span class="monogram">H&amp;G</span></div>
      <div class="tile"><div class="names"><span>Helen</span><span>Gavin</span></div></div>
      <div class="tile"><span class="monogram">H&amp;G</span></div>
      <!-- row 3 -->
      <div class="tile"><span class="monogram">H&amp;G</span></div>
      <div class="tile"><div class="names"><span>Helen</span><span>Gavin</span></div></div>
      <div class="tile"><span class="monogram">H&amp;G</span></div>
      <div class="tile"><div class="names"><span>Helen</span><span>Gavin</span></div></div>
      <div class="tile"><span class="monogram">H&amp;G</span></div>
      <div class="tile"><div class="names"><span>Helen</span><span>Gavin</span></div></div>
      <div class="tile"><span class="monogram">H&amp;G</span></div>
      <div class="tile"><div class="names"><span>Helen</span><span>Gavin</span></div></div>
      <!-- row 4 -->
      <div class="tile"><div class="names"><span>Helen</span><span>Gavin</span></div></div>
      <div class="tile"><span class="monogram">H&amp;G</span></div>
      <div class="tile"><div class="names"><span>Helen</span><span>Gavin</span></div></div>
      <div class="tile"><span class="monogram">H&amp;G</span></div>
      <!-- row 5 -->
      <div class="tile"><span class="monogram">H&amp;G</span></div>
      <div class="tile"><div class="names"><span>Helen</span><span>Gavin</span></div></div>
      <div class="tile"><span class="monogram">H&amp;G</span></div>
      <div class="tile"><div class="names"><span>Helen</span><span>Gavin</span></div></div>
      <!-- row 6 -->
      <div class="tile"><div class="names"><span>Helen</span><span>Gavin</span></div></div>
      <div class="tile"><span class="monogram">H&amp;G</span></div>
      <div class="tile"><div class="names"><span>Helen</span><span>Gavin</span></div></div>
      <div class="tile"><span class="monogram">H&amp;G</span></div>
      <!-- row 7 -->
      <div class="tile"><span class="monogram">H&amp;G</span></div>
      <div class="tile"><div class="names"><span>Helen</span><span>Gavin</span></div></div>
      <div class="tile"><span class="monogram">H&amp;G</span></div>
      <div class="tile"><div class="names"><span>Helen</span><span>Gavin</span></div></div>
      <!-- row 8 -->
      <div class="tile"><div class="names"><span>Helen</span><span>Gavin</span></div></div>
      <div class="tile"><span class="monogram">H&amp;G</span></div>
      <div class="tile"><div class="names"><span>Helen</span><span>Gavin</span></div></div>
      <div class="tile"><span class="monogram">H&amp;G</span></div>
      <!-- row 9 -->
      <div class="tile"><span class="monogram">H&amp;G</span></div>
      <div class="tile"><div class="names"><span>Helen</span><span>Gavin</span></div></div>
      <div class="tile"><span class="monogram">H&amp;G</span></div>
      <div class="tile"><div class="names"><span>Helen</span><span>Gavin</span></div></div>
      <!-- row 10 -->
      <div class="tile"><div class="names"><span>Helen</span><span>Gavin</span></div></div>
      <div class="tile"><span class="monogram">H&amp;G</span></div>
      <div class="tile"><div class="names"><span>Helen</span><span>Gavin</span></div></div>
      <div class="tile"><span class="monogram">H&amp;G</span></div>
      <div class="tile"><div class="names"><span>Helen</span><span>Gavin</span></div></div>
      <div class="tile"><span class="monogram">H&amp;G</span></div>
      <div class="tile"><div class="names"><span>Helen</span><span>Gavin</span></div></div>
      <div class="tile"><span class="monogram">H&amp;G</span></div>
      <!-- row 11 -->
      <div class="tile"><span class="monogram">H&amp;G</span></div>
      <div class="tile"><div class="names"><span>Helen</span><span>Gavin</span></div></div>
      <div class="tile"><span class="monogram">H&amp;G</span></div>
      <div class="tile"><div class="names"><span>Helen</span><span>Gavin</span></div></div>
      <div class="tile"><span class="monogram">H&amp;G</span></div>
      <div class="tile"><div class="names"><span>Helen</span><span>Gavin</span></div></div>
      <div class="tile"><span class="monogram">H&amp;G</span></div>
      <div class="tile"><div class="names"><span>Helen</span><span>Gavin</span></div></div>
      <!-- row 12 -->
      <div class="tile"><div class="names"><span>Helen</span><span>Gavin</span></div></div>
      <div class="tile"><span class="monogram">H&amp;G</span></div>
      <div class="tile"><div class="names"><span>Helen</span><span>Gavin</span></div></div>
      <div class="tile"><span class="monogram">H&amp;G</span></div>
      <div class="tile"><div class="names"><span>Helen</span><span>Gavin</span></div></div>
      <div class="tile"><span class="monogram">H&amp;G</span></div>
      <div class="tile"><div class="names"><span>Helen</span><span>Gavin</span></div></div>
      <div class="tile"><span class="monogram">H&amp;G</span></div>
    </div>
  </section>
</main>
</body>
</html>
```